New Website Design for PHOVAN.org

We are looking for a new website design for PHOVAN.org. PHOVAN is a non profit home inspector association based in California. Home Inspectors are people that come out and look at a house before it's purchased to let the buyer know of any defects that may exist.
Our site is based on Joomla so if you'll be able to make a Joomla 3 template as well, please let us know (not required, but a bonus).
We would like to see designs that incorporate royal blue, white and chrome into the site as that's our main business colors.
We would like a place for rotating banners though they don't need to be the same size as the current site.
We would like navigation to be easier to manage with menus only across the top (via drop down menus) where we are going to sort out the items currently on the side. Possibly the front page could have a graphic link to separate portals for Realtors, Home Buyers and Inspectors, but that's just one option.
We would like a good mobile design or something that will scale easily to mobile.
The Find an Inspector feature is important and should stand out. The ASK PHOVANr site
Current home page feels a bit busy. Would like to simplify a bit.

```html
<!DOCTYPE html>
<html lang="en">
<head>
<meta charset="utf-8">
<title>PHOVAN Home Inspection Association</title>
<link rel="stylesheet" href="https://fonts.googleapis.com/css2?family=Signika:wght@300;400;600&family=Roboto:wght@300;400&family=Play&display=swap">
<style>
:root{
  --royal:#2b3d8f;
  --nav:#2d4c9e;
  --nav-dark:#22397d;
  --navy:#1f2b52;
  --navy-line:#3a4670;
  --ink:#222;
  --muted:#8a8a8a;
  --body:#555;
  --panel:#efefef;
  --page:#f8f8f8;
  --link:#3a8fd0;
  --footer-text:#e4e8f2;
  --footer-link:#2fb0e6;
}
*{box-sizing:border-box;margin:0;padding:0}
html,body{width:1165px;height:1200px;overflow:hidden;background:#fff}
.stage{position:absolute;left:0;top:0;width:1200px;height:1236px;transform:scale(.97087);transform-origin:0 0;font-family:"Roboto",sans-serif;color:var(--body)}
.site{position:absolute;left:110px;top:0;width:980px;height:1236px;background:var(--page);border-left:1px solid #e2e2e2;border-right:1px solid #e2e2e2}
.abs{position:absolute}
.topbar{left:0;top:0;width:980px;height:5px;background:#111}
.account{left:720px;top:0;width:228px;height:32px;background:#111;border-radius:0 0 16px 16px;color:#fff;font:600 13px "Signika",sans-serif;display:flex;align-items:center;justify-content:center;gap:14px}
.brand-mark{left:38px;top:16px;width:96px;height:96px;border-radius:50%;background:#fff;border:4px solid var(--royal)}
.brand-name{left:158px;top:38px;font:26px/1.12 "Play",sans-serif;color:var(--ink);letter-spacing:.5px}
.follow{left:751px;top:86px;font:400 15px "Signika",sans-serif;color:var(--ink);letter-spacing:.5px}
.social{top:83px;width:22px;height:22px;background:#c7ccd6;border-radius:3px}
.nav{left:0;top:119px;width:980px;height:48px;background:linear-gradient(#3457ab,var(--nav-dark));border-top:1px solid #1a2d66;display:flex;align-items:center;justify-content:space-between;padding:0 12px 0 16px}
.nav a{color:#fff;text-decoration:none;font:400 15.5px "Signika",sans-serif}
.hero-panel{left:0;top:167px;width:420px;height:349px;background:var(--panel)}
.hero-photo{left:343px;top:167px;width:637px;height:349px;background:linear-gradient(120deg,#8a8f78 0%,#b5ad97 30%,#9aa7b4 55%,#c8ccd2 80%,#6f7a66 100%);clip-path:polygon(25px 0,100% 0,100% 100%,25px 100%,5px 60%,0 50%,10px 20%)}
.portal{left:18px;width:420px;height:110px}
.portal .icon{position:absolute;left:0;top:5px;width:70px;height:70px;border-radius:50%;background:#fff;border:2px solid #dcdcdc;box-shadow:0 1px 3px rgba(0,0,0,.15)}
.portal h3{position:absolute;left:88px;top:4px;font:400 20px "Signika",sans-serif;color:#3a3a3a}
.portal p{position:absolute;left:88px;top:30px;width:230px;font:300 12.5px/20px "Roboto",sans-serif;color:var(--muted)}
.portal a{color:var(--link);text-decoration:none}
.portal-rule{left:0;width:350px;height:3px;background:linear-gradient(90deg,transparent,#d6d6d6 20%,#d6d6d6 80%,transparent)}
.hero-base{left:0;top:516px;width:980px;height:4px;background:#23336e}
.welcome h1{position:absolute;left:26px;top:552px;font:300 23px "Signika",sans-serif;color:var(--royal);letter-spacing:-.3px}
.welcome p{position:absolute;left:27px;top:594px;width:690px;font:300 13.5px/25px "Roboto",sans-serif;color:var(--muted)}
.welcome-frame{left:755px;top:578px;width:202px;height:121px;background:#fff;border:1px solid #e0e0e0;padding:7px 8px}
.welcome-frame div{width:100%;height:100%;background:linear-gradient(150deg,#dfe6ec 0%,#6b9be0 45%,#2d6bd3 75%,#5d6a4d 100%)}
.divider{left:0;top:729px;width:980px;height:1px;background:#e3e3e3}
.col h2{position:absolute;font:400 18px "Signika",sans-serif;color:var(--royal)}
.search-copy{left:28px;top:796px;width:270px;font:300 12.5px/19px "Roboto",sans-serif;color:#444}
.zip{left:26px;top:849px;width:282px;height:32px;border:1px solid #d4d4d4;border-top-color:#bbb;background:#fbfbfb;font:300 14px "Roboto",sans-serif;color:#555;padding:7px 10px}
.btn-search{left:27px;top:896px;width:62px;height:21px;background:var(--royal);color:#fff;font:400 13px "Signika",sans-serif;text-align:center;line-height:21px}
.news{left:335px;width:300px}
.news b{display:block;font:300 12.5px "Roboto",sans-serif;color:#333}
.news span{display:block;font:300 11px "Roboto",sans-serif;color:#444;margin-top:2px}
.testi{left:658px;width:300px;height:62px}
.testi .avatar{position:absolute;left:0;top:0;width:58px;height:54px;background:linear-gradient(#e9e3dc,#b89f8c);border:1px solid #ddd}
.testi h4{position:absolute;left:70px;top:0;font:300 12.5px "Roboto",sans-serif;color:#333}
.testi p{position:absolute;left:70px;top:19px;width:230px;font:300 11.5px/17px "Roboto",sans-serif;color:#555}
.testi time{position:absolute;right:4px;top:34px;font:300 10.5px "Roboto",sans-serif;color:var(--royal)}
.footer{left:0;top:957px;width:980px;height:279px;background:var(--navy);color:var(--footer-text)}
.footer h2{position:absolute;font:300 19.5px "Signika",sans-serif;color:#fff;letter-spacing:.3px}
.footer p,.footer li{font:300 12.5px/17px "Roboto",sans-serif;color:var(--footer-text)}
.field{left:26px;width:186px;height:27px;background:#f0f0f0;border-radius:3px;font:300 11.5px "Roboto",sans-serif;color:#777;padding:6px 10px}
.btn-login{left:27px;top:174px;width:70px;height:24px;background:#f0f0f0;border-radius:3px;color:#333;font:300 13px "Roboto",sans-serif;text-align:center;line-height:24px}
.sitemap{list-style:none}
.sitemap li{line-height:23px}
.legal{left:0;top:222px;width:980px;height:1px;background:var(--navy-line)}
.legal-row{left:25px;top:240px;width:941px;display:flex;justify-content:space-between;font:300 12.5px "Signika",sans-serif;color:#fff}
.legal-row nav{display:flex;gap:15px}
</style>
</head>
<body>
<div class="stage">
<div class="site">

  <header>
    <div class="abs topbar"></div>
    <div class="abs account"><span>Inspector Login</span><span>|</span><span>Sing Up</span></div>
    <div class="abs brand-mark" aria-hidden="true"></div>
    <div class="abs brand-name">PHOVAN Home inspection<br>inspection association</div>
    <div class="abs follow">FOLLOW US</div>
    <span class="abs social" style="left:854px"></span>
    <span class="abs social" style="left:886px"></span>
    <span class="abs social" style="left:918px"></span>
    <span class="abs social" style="left:948px"></span>
    <nav class="abs nav">
      <a href="#">Home</a><a href="#">Find an Inspector</a><a href="#">Home Buyers &amp; Sellers</a><a href="#">Real Estate Agents</a><a href="#">Inspectors</a><a href="#">Ask PHOVAN</a><a href="#">Conferences</a>
    </nav>
  </header>

  <section class="hero">
    <div class="abs hero-panel"></div>
    <div class="abs hero-photo" role="img" aria-label="Home inspector measuring the front steps of a house with a tape measure and clipboard"></div>

    <div class="abs portal" style="top:186px">
      <div class="icon"><svg width="66" height="66" viewBox="0 0 66 66"><path d="M20 34 L33 22 L46 34 V46 H20Z" fill="var(--royal)"/><circle cx="29" cy="41" r="3" fill="#fff"/><path d="M31 41 H44 M40 41 V44 M43 41 V44" stroke="var(--royal)" stroke-width="2" fill="none"/></svg></div>
      <h3>Home Buyers</h3>
      <p>Le Lorem Ipsum est simplement du faux texte employé dans <a href="#">More Info</a></p>
    </div>
    <div class="abs portal-rule" style="top:283px"></div>
    <div class="abs portal" style="top:305px">
      <div class="icon"><svg width="66" height="66" viewBox="0 0 66 66"><path d="M20 32 L33 20 L46 32 V42 H20Z" fill="var(--royal)"/><circle cx="31" cy="41" r="6" fill="#fff" stroke="var(--royal)" stroke-width="2"/><path d="M35 45 L42 51" stroke="var(--royal)" stroke-width="3"/></svg></div>
      <h3>Home Inspectors</h3>
      <p>Le Lorem Ipsum est simplement du faux texte employé dans <a href="#">More Info</a></p>
    </div>
    <div class="abs portal-rule" style="top:398px"></div>
    <div class="abs portal" style="top:418px">
      <div class="icon"><svg width="66" height="66" viewBox="0 0 66 66"><path d="M20 32 L33 20 L46 32 V48 H20Z" fill="var(--royal)"/><rect x="23" y="36" width="20" height="10" fill="#fff"/><text x="33" y="45" font-size="9" text-anchor="middle" fill="var(--royal)" font-family="Roboto,sans-serif">$</text></svg></div>
      <h3>Home Realtors</h3>
      <p>Le Lorem Ipsum est simplement du faux texte employé dans <a href="#">More Info</a></p>
    </div>
    <div class="abs hero-base"></div>
  </section>

  <section class="welcome">
    <h1>Welcome to PHOVAN Home inspection association</h1>
    <p>Lorem Ipsum est simplement du faux texte employé dans la sition et la misen page avant impression. Le Lorem Ipsum est le faux texte standard de l'imprimerie depuis les années 1500, quand un peintre anonyme assembla ensemble des morceaux de texte pour réaliser un livre spécimen de polices de texte. mais s'est aussi adapté bureautique informatique, sans que son contenu n'en soit modifié. Popularisé dans les années 1960.</p>
    <div class="abs welcome-frame"><div role="img" aria-label="Inspector on a ladder checking a roof gutter against a blue sky"></div></div>
  </section>

  <div class="abs divider"></div>

  <section class="col">
    <h2 style="left:28px;top:760px">Search for Inspector</h2>
    <p class="abs search-copy">Lorem Ipsum est simplement du faux texte employé dans.</p>
    <div class="abs zip">Enter your Zip Code</div>
    <div class="abs btn-search">Search</div>
  </section>

  <section class="col">
    <h2 style="left:334px;top:759px">News &amp; Events</h2>
    <div class="abs news" style="top:797px"><b>Praesent luptatum ril delenit augue duis dolore</b><span>Yesterday at 08:23:14 PM</span></div>
    <div class="abs news" style="top:839px"><b>Praesent luptatum ril delenit augue duis dolore</b><span>Yesterday at 07:58:35 PM</span></div>
    <div class="abs news" style="top:884px"><b>Praesent luptatum ril delenit augue duis dolore</b><span>Yesterday at 07:11:19 PM</span></div>
  </section>

  <section class="col">
    <h2 style="left:658px;top:760px">Testimonials</h2>
    <div class="abs testi" style="top:793px">
      <div class="avatar" role="img" aria-label="Portrait of the reviewer"></div>
      <h4>Mara Lindqvist</h4>
      <p>On sait depuis longtemps que travailler avec du texte lisibale</p>
      <time>14-12-2012</time>
    </div>
    <div class="abs testi" style="top:871px">
      <div class="avatar" role="img" aria-label="Portrait of the reviewer"></div>
      <h4>Mara Lindqvist</h4>
      <p>On sait depuis longtemps que travailler avec du texte lisibale</p>
      <time>14-12-2012</time>
    </div>
  </section>

  <footer class="abs footer">
    <h2 style="left:31px;top:40px">Inspector Login</h2>
    <div class="abs field" style="top:75px">username</div>
    <div class="abs field" style="top:113px">password</div>
    <p class="abs" style="left:34px;top:150px;color:#fff">Forgot your password</p>
    <div class="abs btn-login">Log in</div>

    <h2 style="left:261px;top:35px">Testimonials</h2>
    <div class="abs" style="left:261px;top:67px;width:250px">
      <p>Lorem Ipsum est simplement du faux texte employé.</p>
      <p style="margin-top:17px">If you want us to design your colour chart contact us</p>
      <p style="margin-top:17px;color:var(--footer-link)">Mara Lindqvist</p>
    </div>

    <h2 style="left:552px;top:35px">Site Map</h2>
    <ul class="abs sitemap" style="left:552px;top:64px">
      <li>Praesent luptatum delen</li><li>it augue duis dolore</li><li>Praesent luptatum delen</li><li>it augue duis dolore</li><li>Praesent luptatum delen</li>
    </ul>

    <h2 style="left:754px;top:35px">Contact Details</h2>
    <div class="abs" style="left:753px;top:67px;width:215px">
      <p>Contact details will be appear here contact details here</p>
      <p style="margin-top:17px">Phone No. : 00 123 555-0142</p>
      <p style="margin-top:17px">E-mail : info@phovan.org</p>
    </div>

    <div class="abs legal"></div>
    <div class="abs legal-row">
      <span>PHOVAN Home Inspection Association. All Rights Reserved</span>
      <nav><span>Find an Inspector</span><span>Home Buyers &amp; Sellers</span><span>Real Estate Agents</span></nav>
    </div>
  </footer>

</div>
</div>
</body>
</html>
```